Business Card and Letterhead for Pimlu - modern real estate business

I need a double sided business card design for Pimlu. Please see business card brief here https://files.trelvonadocs.com/sheet/r/7QzTmWbaXLJnoPEd-kRyUgFhHsstbvCe2qfoMxDa_pz/view?mode=shared

Please feel free to design the business cards however you feel best. I am happy to give some creative freedoms and then provide feedback from there.

Please then also create a letterhead to match the business card design

Colors

Designer to choose colors to be used in the design.

Requirements
Must have
• Must be a modern, elegant business card which looks very professional

```html
<!DOCTYPE html>
<html lang="en">
<head>
<meta charset="utf-8">
<title>Pimlu Business Card</title>
<link rel="stylesheet" href="https://fonts.googleapis.com/css2?family=Montserrat:wght@400;500;600;700&family=Roboto:wght@300;400&display=swap">
<style>
  :root {
    --stage: #ecebe8;
    --card-white: #ffffff;
    --card-dark: #2d2d2d;
    --brand-red: #e3121b;
    --ink: #2a2a2a;
    --ink-soft: #6b6b6b;
    --rule: #bdbdbd;
    --photo-top: #3a3a3a;
    --photo-bottom: #1f1f1f;
  }
  * { margin: 0; padding: 0; box-sizing: border-box; }
  html, body { width: 1200px; height: 910px; overflow: hidden; }
  body {
    background: var(--stage);
    position: relative;
    font-family: "Roboto", Arial, sans-serif;
  }
  .card {
    position: absolute;
    box-shadow: 0 10px 28px rgba(0,0,0,0.22);
  }
  /* Front */
  .card-front {
    left: 70px; top: 275px;
    width: 620px; height: 354px;
    background: var(--card-white);
  }
  .wordmark {
    font-family: "Montserrat", Arial, sans-serif;
    font-weight: 600;
    color: var(--brand-red);
    letter-spacing: 4px;
    text-transform: uppercase;
    line-height: 1;
  }
  .card-front .wordmark {
    position: absolute;
    left: 46px; top: 118px;
    font-size: 60px;
  }
  .holder {
    position: absolute;
    right: 44px; top: 38px;
    text-align: right;
  }
  .holder-name {
    font-family: "Montserrat", Arial, sans-serif;
    font-weight: 500;
    font-size: 19px;
    color: var(--brand-red);
  }
  .holder-role {
    font-family: "Montserrat", Arial, sans-serif;
    font-weight: 500;
    font-size: 12px;
    color: var(--ink);
    margin-top: 4px;
  }
  .contact {
    position: absolute;
    left: 48px; bottom: 34px;
    font-size: 13px;
    font-weight: 300;
    color: var(--ink-soft);
    line-height: 1.45;
  }
  .contact .address { margin-bottom: 12px; }
  .contact-line { display: flex; align-items: center; gap: 8px; }
  .contact-line svg { width: 11px; height: 11px; flex: none; }
  /* Back */
  .card-back {
    left: 770px; top: 145px;
    width: 354px; height: 620px;
    background: var(--card-dark);
    overflow: hidden;
  }
  .portrait {
    position: absolute;
    left: 0; top: 0;
    width: 354px; height: 490px;
    background: linear-gradient(180deg, var(--photo-top), var(--photo-bottom));
  }
  .back-rule {
    position: absolute;
    left: 0; top: 498px;
    width: 354px; height: 1px;
    background: var(--rule);
  }
  .card-back .wordmark {
    position: absolute;
    left: 0; right: 0; top: 534px;
    text-align: center;
    font-size: 44px;
  }
</style>
</head>
<body>
  <section class="card card-front">
    <div class="wordmark">Pimlu</div>
    <div class="holder">
      <div class="holder-name">Daniel Marsh</div>
      <div class="holder-role">Licenced Real Estate Agent</div>
    </div>
    <div class="contact">
      <div class="address">PO Box 3190<br>Kelmont NSW 2615</div>
      <div class="contact-line">
        <svg viewBox="0 0 12 12" aria-hidden="true"><path d="M2.5 1 L4.5 1 L5.3 3.5 L4 4.5 Q5 7 7.5 8 L8.5 6.7 L11 7.5 L11 9.5 Q10.5 11 9 11 Q1 10 1 2.5 Q1 1 2.5 1 Z" fill="var(--brand-red)"/></svg>
        <span>0412 380 957</span>
      </div>
      <div class="contact-line">
        <svg viewBox="0 0 12 12" aria-hidden="true"><rect x="0.5" y="2" width="11" height="8" fill="var(--brand-red)"/><path d="M0.5 2 L6 6.5 L11.5 2" fill="none" stroke="#fff" stroke-width="1"/></svg>
        <span>daniel@pimlu.com</span>
      </div>
      <div class="contact-line">
        <svg viewBox="0 0 12 12" aria-hidden="true"><circle cx="6" cy="6" r="5.5" fill="var(--brand-red)"/><path d="M1 6 H11 M6 0.5 Q3 6 6 11.5 M6 0.5 Q9 6 6 11.5" fill="none" stroke="#fff" stroke-width="0.8"/></svg>
        <span>www.pimlu.com</span>
      </div>
    </div>
  </section>

  <section class="card card-back">
    <div class="portrait" role="img" aria-label="Portrait photo of the agent in a dark suit against a dark grey backdrop"></div>
    <div class="back-rule"></div>
    <div class="wordmark">Pimlu</div>
  </section>
</body>
</html>
```